Business Card & Letterhead Design

We a financial advice company based in Australia. We provide advice to wealthy farmers.

We are changing our business name FROM Brightvale Financial TO Tallowmere Wealth and we need a new letterhead and double sided business card design

Attached is designs from our previous branding (Brightvale Financial) as it includes all the details we require on the new Tallowmere Wealth business cards and letterhead.

Need extra days to review

```html
<!DOCTYPE html>
<html lang="en">
<head>
<meta charset="utf-8">
<title>Tallowmere Wealth – Business Card</title>
<link href="https://fonts.googleapis.com/css2?family=Cinzel:wght@400;500&family=Montserrat:wght@400;500&display=swap" rel="stylesheet">
<style>
  :root {
    --page: #d9dcdf;
    --front: #5c6871;
    --back: #4a4b4d;
    --accent: #6f7c86;
    --accent-deep: #5c6871;
    --ink: #ffffff;
    --ink-soft: #e4e7ea;
    --icon: #8a949b;
  }
  * { box-sizing: border-box; margin: 0; padding: 0; }
  html, body { width: 1200px; height: 900px; overflow: hidden; }
  body { background: var(--page); position: relative; font-family: "Montserrat", sans-serif; color: var(--ink); }

  .card {
    position: absolute; left: 270px; width: 660px; height: 400px;
    border-radius: 22px; overflow: hidden;
    box-shadow: 0 10px 30px rgba(0,0,0,0.25);
  }
  .card--front { top: 38px; background: var(--front); }
  .card--back { top: 462px; background: var(--back); }

  /* front */
  .front__brand { position: absolute; left: 48px; top: 92px; }
  .brand-name { font-family: "Cinzel", serif; font-size: 27px; letter-spacing: 1px; color: var(--ink); line-height: 1; }
  .brand-tagline { font-size: 9.5px; letter-spacing: 3.2px; color: var(--ink-soft); margin-top: 4px; text-transform: uppercase; }
  .services { position: absolute; left: 48px; top: 168px; list-style: none; }
  .services li { display: flex; align-items: center; gap: 12px; font-family: "Cinzel", serif; font-size: 17px; letter-spacing: 0.5px; margin-bottom: 8px; }
  .services svg { width: 18px; height: 18px; flex: none; }
  .licensee { position: absolute; left: 48px; top: 308px; font-size: 13px; line-height: 1.55; color: var(--ink-soft); }
  .front__ring { position: absolute; right: 70px; top: 58px; width: 200px; height: 200px; border: 4px solid var(--ink); border-radius: 50%; }

  /* back */
  .back__ring { position: absolute; left: 108px; top: 56px; width: 74px; height: 74px; border: 3px solid var(--ink); border-radius: 50%; }
  .back__brand { position: absolute; left: 48px; top: 146px; }
  .back__brand .brand-name { font-size: 22px; }
  .back__brand .brand-tagline { font-size: 8px; letter-spacing: 2.6px; }
  .back__rule { position: absolute; left: 48px; width: 290px; top: 196px; height: 1px; background: var(--ink-soft); }
  .contacts { position: absolute; left: 48px; top: 214px; list-style: none; }
  .contacts li { display: flex; align-items: center; gap: 14px; font-size: 15px; line-height: 1; margin-bottom: 8px; }
  .contacts svg { width: 13px; height: 13px; flex: none; fill: var(--icon); }

  .profile { position: absolute; right: 40px; top: 34px; text-align: right; }
  .motto { font-family: "Cinzel", serif; font-size: 12px; letter-spacing: 0.5px; color: var(--ink-soft); margin-bottom: 10px; }
  .person { font-family: "Cinzel", serif; font-size: 18px; }
  .person small { font-family: "Montserrat", sans-serif; font-size: 12px; color: var(--ink-soft); }
  .role { font-size: 12.5px; line-height: 1.5; color: var(--ink-soft); }
  .profile__rule { position: absolute; right: 40px; top: 148px; width: 270px; height: 1px; background: var(--ink-soft); }
  .address { position: absolute; right: 40px; top: 162px; text-align: right; font-size: 13px; line-height: 1.5; color: var(--ink-soft); }
  .slogan { position: absolute; right: 40px; top: 262px; font-family: "Cinzel", serif; font-size: 12.5px; letter-spacing: 0.5px; }
  .back__accent { position: absolute; left: 0; top: 0; width: 660px; height: 400px; }
</style>
</head>
<body>

<section class="card card--front" aria-label="Business card front">
  <div class="front__brand">
    <div class="brand-name">TALLOWMERE WEALTH</div>
    <div class="brand-tagline">Strategic Financial Advice</div>
  </div>
  <ul class="services">
    <li><svg viewBox="0 0 18 18" fill="none" stroke="#fff" stroke-width="1.4"><circle cx="9" cy="9" r="7.5"/><path d="M6 12V9M9 12V6M12 12V8"/></svg>Life &amp; TPD Insurance</li>
    <li><svg viewBox="0 0 18 18" fill="none" stroke="#fff" stroke-width="1.4"><circle cx="9" cy="9" r="7.5"/><path d="M6 12V9M9 12V6M12 12V8"/></svg>Income Protection</li>
    <li><svg viewBox="0 0 18 18" fill="none" stroke="#fff" stroke-width="1.4"><circle cx="9" cy="9" r="7.5"/><path d="M6 12V9M9 12V6M12 12V8"/></svg>Financial Planning</li>
    <li><svg viewBox="0 0 18 18" fill="none" stroke="#fff" stroke-width="1.4"><circle cx="9" cy="9" r="7.5"/><path d="M6 12V9M9 12V6M12 12V8"/></svg>Retirement Planning</li>
  </ul>
  <p class="licensee">Harbourline Financial Planning Limited<br>Australian Financial Services Licensee-License Number 481207</p>
  <div class="front__ring"></div>
</section>

<section class="card card--back" aria-label="Business card back">
  <svg class="back__accent" viewBox="0 0 660 400" aria-hidden="true">
    <polygon points="660,300 660,316 630,316 612,334 612,400 596,400 596,326 622,300" fill="#6f7c86"/>
    <polygon points="612,334 630,316 660,316 660,400 612,400" fill="#5c6871"/>
    <polygon points="0,400 0,390 596,360 596,400" fill="#ffffff"/>
  </svg>

  <div class="back__ring"></div>
  <div class="back__brand">
    <div class="brand-name">TALLOWMERE WEALTH</div>
    <div class="brand-tagline">Strategic Financial Advice</div>
  </div>
  <div class="back__rule"></div>
  <ul class="contacts">
    <li><svg viewBox="0 0 13 13"><rect x="3" y="0" width="7" height="13" rx="1.5"/></svg>0400 555 218</li>
    <li><svg viewBox="0 0 13 13"><path d="M1 4c0-2 2-3 5.5-3S12 2 12 4l-2 1-1-2H4L3 5zM2 12l1.5-6h6L11 12z"/></svg>(07) 5550 1234</li>
    <li><svg viewBox="0 0 13 13"><rect x="1" y="4" width="11" height="8" rx="1"/><rect x="3" y="0" width="7" height="4"/></svg>(07) 5550 6789</li>
    <li><svg viewBox="0 0 13 13"><path d="M0 2h13v9H0z M1 3l5.5 4L12 3" stroke="#4a4b4d" stroke-width="0.8"/></svg>sam@tallowmerewealth.com.au</li>
    <li><svg viewBox="0 0 13 13"><circle cx="6.5" cy="6.5" r="6"/></svg>www.tallowmerewealth.com.au</li>
  </ul>

  <div class="profile">
    <p class="motto">'FINANCIAL PEACE OF MIND'</p>
    <p class="person">SAM CARTER <small>| B.Ag.Ec. Dip F.P. M.Fin.</small></p>
    <p class="role">Managing Director<br>Authorised Representative</p>
  </div>
  <div class="profile__rule"></div>
  <p class="address">Suite 7A, 41 Fennick St<br>Wattle Bend QLD 4188<br>PO Box 3120<br>East Marlowe QLD 4188</p>
  <p class="slogan">A REFERRAL BUILT BUSINESS</p>
</section>

</body>
</html>
```